Tech business card design

We need an amazing business card design for our new business 'Pexla' a marketing tech startup based in Sydney, Australia. We provide an online marketplace for businesses to search and buy advertising media, connect with service providers and learn more about marketing. We wish to communicate 'cool tech', reliability and professionalism and design based around our logo.

Target Market(s)

Business Owners

Contact Information for Business Card

Name
Position
Email Address
Website
Phone Number

Font styles to use
Other font styles liked:
• Avenir & Avenir Next

Colors

Designer to choose colors to be used in the design.

```html
<!DOCTYPE html>
<html lang="en">
<head>
<meta charset="utf-8">
<title>Pexla Business Card</title>
<link rel="stylesheet" href="https://fonts.googleapis.com/css2?family=Open+Sans:wght@400;700;800&display=swap">
<style>
  :root {
    --backdrop: #94a8b2;
    --card-white: #ffffff;
    --navy-band: #243070;
    --divider: #2d3a7a;
    --card-back: #656ba5;
    --ink: #231f20;
    --logo-ink: #0e1235;
  }
  * { margin: 0; padding: 0; box-sizing: border-box; }
  html, body {
    width: 1079px; height: 1200px; overflow: hidden;
    background: var(--backdrop);
    font-family: "Open Sans", Arial, sans-serif;
    color: var(--ink);
  }
  .canvas { position: relative; width: 1079px; height: 1200px; }

  .card-front {
    position: absolute; left: 87px; top: 47px; width: 904px; height: 515px;
    background: var(--card-white); border-radius: 19px; overflow: hidden;
  }
  .card-front .bottom-band {
    position: absolute; left: 0; bottom: 0; width: 100%; height: 34px;
    background: var(--navy-band);
  }
  .identity {
    position: absolute; right: 494px; top: 208px; text-align: right;
  }
  .identity .person-name {
    font-weight: 700; font-size: 32px; line-height: 40px; letter-spacing: 0.2px;
  }
  .identity .person-role {
    font-weight: 400; font-size: 37px; line-height: 44px;
  }
  .divider {
    position: absolute; left: 452px; top: 169px; width: 2px; height: 169px;
    background: var(--divider);
  }
  .contact-list {
    position: absolute; left: 507px; top: 168px; list-style: none;
    font-size: 22.5px; line-height: 38px;
  }
  .contact-list li { display: flex; align-items: center; height: 38px; }
  .contact-list .icon { width: 22px; height: 22px; margin-right: 10px; flex: none; }
  .contact-list .web { letter-spacing: 2.6px; }
  .contact-address {
    position: absolute; left: 507px; top: 277px;
    font-size: 22.5px; line-height: 30px;
  }

  .card-back {
    position: absolute; left: 87px; top: 617px; width: 904px; height: 517px;
    background: var(--card-back); border-radius: 19px;
  }
  .brand-name {
    position: absolute; left: 0; width: 100%; top: 180px; text-align: center;
    font-weight: 800; font-size: 132px; line-height: 150px; letter-spacing: -2px;
    color: var(--logo-ink);
  }
  .back-web {
    position: absolute; left: 0; width: 100%; top: 414px; text-align: center;
    font-size: 28px; letter-spacing: 4px; color: var(--ink);
  }
</style>
</head>
<body>
<div class="canvas">
  <section class="card-front">
    <div class="identity">
      <div class="person-name">JOHN SMITH</div>
      <div class="person-role">Position</div>
    </div>
    <div class="divider"></div>
    <ul class="contact-list">
      <li>
        <svg class="icon" viewBox="0 0 22 22" aria-hidden="true">
          <circle cx="11" cy="11" r="9.5" fill="none" stroke="#231f20" stroke-width="1.6"/>
          <path d="M8 6.5c-1 1-1.2 3 .6 5.6s3.8 3.8 5.2 3.4l1-1.4-2-1.6-1 .8c-.8-.4-2-1.8-2.3-2.8l.9-.9-1-2.3z" fill="#231f20"/>
        </svg>
        <span>012-345-6789</span>
      </li>
      <li>
        <svg class="icon" viewBox="0 0 22 22" aria-hidden="true">
          <rect x="1" y="5" width="20" height="13" fill="#231f20"/>
          <path d="M1.5 5.5L11 13l9.5-7.5M1.5 17.5l7-6M20.5 17.5l-7-6" fill="none" stroke="#fff" stroke-width="1.3"/>
        </svg>
        <span>info@pexla.com</span>
      </li>
      <li>
        <svg class="icon" viewBox="0 0 22 22" aria-hidden="true">
          <g fill="none" stroke="#231f20" stroke-width="1.5">
            <circle cx="11" cy="11" r="9.5"/>
            <ellipse cx="11" cy="11" rx="4.3" ry="9.5"/>
            <path d="M1.5 11h19M3 6h16M3 16h16M11 1.5v19"/>
          </g>
        </svg>
        <span class="web">www.pexla.com</span>
      </li>
    </ul>
    <address class="contact-address" style="font-style:normal">
      Street name City Name,<br>Zipcode,012345
    </address>
    <div class="bottom-band"></div>
  </section>

  <section class="card-back">
    <div class="brand-name">Pexla</div>
    <div class="back-web">www.pexla.com</div>
  </section>
</div>
</body>
</html>
```